Catalogue Design Project

We need a catalog design for a new private university called Redwell Institute Bayshore (see website www.rwi-bs.org). The catalog should be about 30 pages maximum and will include items such as General Information, Academic schedule, department descriptions, program descriptions, course descriptions, school policies, student services, admissions, San diego Lifestyle, etc.
I will provide the text but I need a professional design with regard to page layouts. I have provided some examples.
Ok, i posted the catalog content, just missing course descriptions.
Target Market(s)
Young Professionals, Foreign Students
Industry/Entity Type
University
Look and feel
Each slider illustrates characteristics of the customer's brand and the style your logo design should communicate.

```html
<!DOCTYPE html>
<html lang="en">
<head>
<meta charset="utf-8">
<title>Academic Calendar – Redwell Institute Bayshore</title>
<link href="https://fonts.googleapis.com/css2?family=Carlito:wght@400;700&display=swap" rel="stylesheet">
<style>
  :root {
    --ink: #1a1a1a;
    --accent: #2f5d94;
    --rule: #8aa6c8;
    --row: #f1f1f1;
    --border: #3c3c3c;
    --muted: #9a9a9a;
    --paper: #ffffff;
  }
  * { margin: 0; padding: 0; box-sizing: border-box; }
  html, body { width: 927px; height: 1200px; overflow: hidden; background: var(--paper); }
  body { font-family: "Carlito", "Calibri", sans-serif; color: var(--ink); position: relative; }

  .header-photo {
    position: absolute; left: 560px; top: 0; width: 367px; height: 150px;
    background: linear-gradient(100deg, #ffffff 0%, #eef1f4 35%, #dfe4ea 70%, #d3d9e0 100%);
  }
  .header-dots { position: absolute; left: 58px; top: 56px; }
  .page-title {
    position: absolute; left: 0; width: 927px; top: 94px;
    text-align: center; font-size: 31px; font-weight: 400; letter-spacing: 0.5px;
  }
  .title-bar { position: absolute; left: 305px; top: 134px; width: 318px; height: 16px; background: var(--accent); }
  .header-rule { position: absolute; left: 0; top: 151px; width: 927px; height: 2px; background: var(--rule); }

  .term { position: absolute; left: 79px; width: 803px; }
  .term-heading {
    display: flex; justify-content: space-between; font-size: 19px; height: 26px;
    white-space: nowrap;
  }
  .schedule { width: 100%; border-collapse: collapse; font-size: 19px; }
  .schedule td {
    height: 34.8px; background: var(--row); border: 1.5px solid var(--border);
    padding: 2px 0 0 0; vertical-align: middle;
  }
  .schedule .date { width: 307px; padding-left: 30px; }
  .schedule .event { padding-left: 36px; }

  .footer-rule { position: absolute; left: 0; top: 1158px; width: 927px; height: 1.5px; background: var(--rule); }
  .footer-note {
    position: absolute; right: 41px; top: 1171px; font-size: 12.5px; color: var(--muted); letter-spacing: 0.3px;
  }
</style>
</head>
<body>
  <div class="header-photo" role="img" aria-label="Soft-focus photo of a wall calendar page"></div>
  <svg class="header-dots" width="156" height="34" viewBox="0 0 156 34" role="img" aria-label="Decorative dot pattern">
    <rect width="156" height="34" rx="12" fill="#a9b4c2"/>
  </svg>

  <h1 class="page-title">ACADEMIC CALENDAR</h1>
  <div class="title-bar"></div>
  <div class="header-rule"></div>

  <section class="term" style="top:232px">
    <div class="term-heading"><span>2012 Fall Quarter:&nbsp; September 4th, 2012 – December 23, 2012</span><span>Enrollment Deadline: 8/17/12</span></div>
    <table class="schedule">
      <tr><td class="date">Tuesday, September 4</td><td class="event">Session A Begins</td></tr>
      <tr><td class="date">Sunday, September 9</td><td class="event">Deadline to Add/Drop Session A</td></tr>
      <tr><td class="date">Sunday, October 28</td><td class="event">Session A Ends</td></tr>
      <tr><td class="date">Monday, October 29</td><td class="event">Session B Begins</td></tr>
      <tr><td class="date">Sunday, November 4</td><td class="event">Deadline to Add/Drop Session B</td></tr>
      <tr><td class="date">Sunday, December 23</td><td class="event">Session B Ends</td></tr>
    </table>
  </section>

  <section class="term" style="top:515px">
    <div class="term-heading"><span>2013 Winter Quarter:&nbsp; January 7, 2013 – March 3, 2013</span><span>Enrollment Deadline: 12/23/12</span></div>
    <table class="schedule">
      <tr><td class="date">Monday, January 7</td><td class="event">Session A Begins</td></tr>
      <tr><td class="date">Sunday, January 13</td><td class="event">Deadline to Add/Drop Session A</td></tr>
      <tr><td class="date">March 3, 2013</td><td class="event">Session A Ends</td></tr>
    </table>
  </section>

  <section class="term" style="top:690px">
    <div class="term-heading"><span>2013 Spring Semester:&nbsp; March 11, 2013 – June 30, 2013</span><span>Enrollment Deadline: 2/24/13</span></div>
    <table class="schedule">
      <tr><td class="date">Monday, March 11</td><td class="event">Session A Begins</td></tr>
      <tr><td class="date">Sunday, March 17</td><td class="event">Deadline to Add/Drop Session A</td></tr>
      <tr><td class="date">Sunday, May 5</td><td class="event">Session A Ends</td></tr>
      <tr><td class="date">Monday, May 6</td><td class="event">Session B Begins</td></tr>
      <tr><td class="date">Sunday, May 12</td><td class="event">Deadline to Add/Drop Session B</td></tr>
      <tr><td class="date">Sunday, June 30</td><td class="event">Session B Ends</td></tr>
    </table>
  </section>

  <section class="term" style="top:966px">
    <div class="term-heading"><span>2013 Summer Semester:&nbsp; July 8, 2013 – September 1, 2013</span><span>Enrollment Deadline: 6/16/13</span></div>
    <table class="schedule">
      <tr><td class="date">Monday, July 8</td><td class="event">Session A Begins</td></tr>
      <tr><td class="date">Sunday, July 14</td><td class="event">Deadline to Add/Drop Session A</td></tr>
      <tr><td class="date">Sunday, September 1</td><td class="event">Session A Ends</td></tr>
    </table>
  </section>

  <div class="footer-rule"></div>
  <div class="footer-note">4::: REDWELL INSTITUTE</div>
</body>
</html>
```